Corporate Reception Invite (Bluebird Gathering: Amberglow Night)

I am looking for an invitation to use in Constant Contact for an upcoming reception. I have attached the company logo and a hero image from the reception location that may work well. Lastly, I attached an example from last year's invite for reference. Event details:

Bluebird Gathering: Amberglow Night @ RVQ
October 23rd, 2023 from 6:00 - 8:00 pm
Solmera at The Brisbury, Chicago
1472 W Fenwick St, Chicago, IL 60654
Join PBH & Friends for Cocktails & Conversation
Super casual - come and go as you please. Guests welcome.

Target Market(s)

Corporate audience

Font styles to use
Serif
Script
Other font styles liked:
• No strong preference, but want something elegant, sexy, and corporate

Colors
0054AA
0677BA
7BADD7
CADEEF
E8F1F8

Requirements
Must have
• PBH logo, event details, size: 600 x 1500 pixels

```html
<!DOCTYPE html>
<html lang="en">
<head>
<meta charset="utf-8">
<title>Bluebird Gathering: Amberglow Night — Invitation</title>
<link rel="stylesheet" href="https://fonts.googleapis.com/css2?family=Bebas+Neue&family=Poppins:wght@200;400;500;600;700;800&display=swap">
<style>
  :root {
    --page-bg: #d9d9d9;
    --card-bg: #ffffff;
    --ink-navy: #0c1230;
    --brand-blue: #1f3d8c;
    --sky-blue: #6cc5ee;
    --photo-dark: #1f2530;
    --photo-mid: #46505f;
    --photo-warm: #7a5a3c;
  }
  * { box-sizing: border-box; margin: 0; padding: 0; }
  html, body {
    width: 931px; height: 1200px; overflow: hidden;
    background: var(--page-bg);
    font-family: "Poppins", sans-serif;
  }
  .invite {
    position: absolute; left: 35px; top: 292px;
    width: 860px; height: 615px;
    background: var(--card-bg);
    box-shadow: 4px 5px 8px rgba(0,0,0,.25);
  }
  .event-title {
    position: absolute; left: 0; right: 0; top: 40px;
    text-align: center;
    font-weight: 800; font-size: 52px; line-height: 1;
    color: var(--ink-navy); letter-spacing: -0.5px;
  }
  .edition-band {
    position: absolute; left: 128px; top: 114px; width: 585px; height: 41px;
    background: var(--sky-blue);
    display: flex; align-items: center; justify-content: center;
    font-weight: 600; font-size: 24px; letter-spacing: 0.32em;
    color: var(--ink-navy); padding-left: 0.32em;
  }
  .hero-band {
    position: absolute; left: 0; top: 183px; width: 860px; height: 136px;
    background:
      radial-gradient(ellipse at 28% 80%, rgba(122,90,60,.75), transparent 45%),
      radial-gradient(ellipse at 70% 40%, rgba(120,130,145,.5), transparent 55%),
      linear-gradient(90deg, var(--photo-mid), var(--photo-dark) 40%, var(--photo-mid) 70%, var(--photo-dark));
  }
  .date-day {
    position: absolute; left: 208px; top: 198px;
    font-family: "Bebas Neue", sans-serif; font-size: 114px; line-height: 1;
    color: #fff;
  }
  .date-suffix {
    position: absolute; left: 302px; top: 206px;
    font-size: 15px; font-weight: 500; color: #fff;
  }
  .date-month {
    position: absolute; left: 330px; top: 196px;
    font-weight: 800; font-size: 58px; line-height: 1; color: #fff;
  }
  .date-year {
    position: absolute; left: 332px; top: 254px;
    font-weight: 200; font-size: 31px; line-height: 1; letter-spacing: 0.12em; color: #fff;
  }
  .time-box {
    position: absolute; left: 414px; top: 262px; width: 232px; height: 27px;
    background: var(--sky-blue);
    display: flex; align-items: center; justify-content: center;
    font-size: 16px; color: var(--brand-blue);
  }
  .time-box strong { font-weight: 600; margin-left: 4px; }
  .venue-name {
    position: absolute; left: 0; right: 0; top: 340px;
    text-align: center; font-weight: 700; font-size: 24px; color: var(--brand-blue);
  }
  .venue-address {
    position: absolute; left: 0; right: 0; top: 374px;
    display: flex; justify-content: center; align-items: center; gap: 4px;
    font-size: 17px; color: var(--ink-navy);
  }
  .brand-mark {
    position: absolute; left: 160px; top: 440px; width: 150px; height: 50px;
    display: flex; align-items: center; justify-content: center; gap: 10px;
  }
  .brand-mark .square { width: 22px; height: 22px; background: var(--brand-blue); }
  .brand-mark .name { font-weight: 700; font-size: 38px; color: var(--brand-blue); line-height: 1; }
  .divider {
    position: absolute; left: 323px; top: 414px; width: 1px; height: 96px;
    background: #c8c8c8;
  }
  .host-line {
    position: absolute; left: 349px; top: 418px; height: 37px; display: flex;
  }
  .host-line .host {
    width: 195px; background: var(--sky-blue);
    display: flex; align-items: center; justify-content: center;
    font-family: "Bebas Neue", sans-serif; font-size: 29px; color: var(--ink-navy); padding-top: 3px;
  }
  .host-line .purpose {
    width: 128px; background: var(--brand-blue); color: #fff;
    font-weight: 600; font-size: 11px; line-height: 1.05;
    display: flex; flex-direction: column; justify-content: center; padding-left: 10px;
  }
  .casual-note {
    position: absolute; left: 349px; top: 466px;
    font-weight: 700; font-size: 14.5px; color: var(--ink-navy);
  }
  .guests-note {
    position: absolute; left: 349px; top: 484px;
    font-size: 27px; letter-spacing: 0.3em; color: var(--brand-blue); line-height: 1.1;
  }
  .rsvp-row {
    position: absolute; left: 87px; top: 535px; display: flex; gap: 21px;
  }
  .rsvp-btn {
    width: 214px; height: 42px; border-radius: 13px;
    border: 1.5px solid var(--sky-blue); background: #fff;
    display: flex; align-items: center; justify-content: center;
    font-size: 16px; font-weight: 500; color: var(--ink-navy);
  }
  .rsvp-btn.primary { background: var(--sky-blue); color: #fff; font-weight: 600; }
</style>
</head>
<body>
  <main class="invite">
    <h1 class="event-title">BLUEBIRD GATHERING</h1>
    <div class="edition-band">AMBERGLOW NIGHT @ RVQ</div>

    <div class="hero-band" role="img" aria-label="Dimly lit bar with wine glasses at the venue"></div>
    <div class="date-day">23</div>
    <div class="date-suffix">RD</div>
    <div class="date-month">OCTOBER</div>
    <div class="date-year">2023</div>
    <div class="time-box">FROM |<strong>6:00 – 8:00 PM</strong></div>

    <h2 class="venue-name">SOLMERA AT THE BRISBURY, CHICAGO</h2>
    <p class="venue-address">
      <svg width="12" height="16" viewBox="0 0 12 16" aria-hidden="true">
        <path d="M6 0C2.7 0 0 2.6 0 5.9 0 10.3 6 16 6 16s6-5.7 6-10.1C12 2.6 9.3 0 6 0z" fill="#6cc5ee"/>
        <circle cx="6" cy="6" r="2.3" fill="#fff"/>
      </svg>
      1472 W Fenwick St, Chicago, IL 60654
    </p>

    <div class="brand-mark"><span class="square"></span><span class="name">PBH</span></div>
    <div class="divider"></div>

    <div class="host-line">
      <div class="host">JOIN PBH &amp; FRIENDS</div>
      <div class="purpose"><span>FOR COCKTAILS &amp;</span><span>CONVERSATION</span></div>
    </div>
    <p class="casual-note">SUPER CASUAL – COME &amp; GO AS YOU PLEASE</p>
    <p class="guests-note">GUESTS WELCOME</p>

    <div class="rsvp-row">
      <span class="rsvp-btn primary">Cheers! I’ll be there</span>
      <span class="rsvp-btn">I’ll try to stop by</span>
      <span class="rsvp-btn">Sorry, I can’t make it</span>
    </div>
  </main>
</body>
</html>
```